House flipping business web site needed

pinecrestholdingsgroup.example.
I am a residential developer in Northern NJ and I am looking for a fresh new updated website. I have an intro video about my company being made now. I don't update it very often but I want an easy format that I can add update photos to on projects I have worked on or homes I renovate for sale.

Target Market(s)

investors into my projects so a portfolio , people looking to sell their homes to me.

Industry/Entity Type

Real Estate Development

Number of Pages Required

4 page

Font styles to use
Serif

Colors
33b8a4
39a9d7
cadf82

Requirements
Must have
• space for an intro video about my company
• a portfolio with pictures and information about each project
• Markets we serve- Morris County, NJ
• My logo- already created
• SEO
• Yes I would like this to function over all platforms. Phone, computer, all platforms.
• history and background page
• I am looking for a completed page that I can upload to the site that hosts my website
Nice to have
• I want something creative, easy to navigate. modern.

```html
<!DOCTYPE html>
<html lang="en">
<head>
<meta charset="utf-8">
<title>Pinecrest Holdings Group – Home</title>
<link rel="stylesheet" href="https://fonts.googleapis.com/css2?family=Roboto:wght@400;500&family=Roboto+Condensed:wght@400;700&family=Nothing+You+Could+Do&display=swap">
<style>
  :root{
    --ink:#1f2329;
    --muted:#7a7f86;
    --accent:#3a9bd9;
    --teal:#33b8a4;
    --band-from:#4fb0e6;
    --band-to:#86d3f8;
    --white:#ffffff;
    --hero-dark:#5c5a55;
    --hero-mid:#8f8574;
    --hero-light:#b9b6ae;
  }
  *{box-sizing:border-box;margin:0;padding:0}
  html,body{width:1200px;height:676px;overflow:hidden;background:#fff}
  body{font-family:"Roboto",Arial,sans-serif;color:var(--ink);position:relative}

  .topbar{position:absolute;top:0;left:0;right:0;height:34px;display:flex;align-items:center;justify-content:flex-end;gap:24px;padding-right:48px;font-size:12.5px;color:var(--muted)}
  .topbar .item{display:flex;align-items:center;gap:5px}
  .topbar svg{width:12px;height:12px;fill:var(--muted)}
  .sell-btn{background:var(--teal);color:var(--white);font-family:"Roboto Condensed",Arial,sans-serif;font-size:12.5px;padding:2px 7px;border-radius:3px}
  .social{display:flex;gap:16px}
  .social span{width:9px;height:9px;border-radius:50%;background:var(--muted);display:block}

  .nav{position:absolute;top:34px;left:0;right:0;height:62px;display:flex;justify-content:flex-end;align-items:center;gap:34px;padding-right:40px;font-size:14.5px;font-weight:500;letter-spacing:.2px}
  .nav a{color:var(--ink);text-decoration:none}
  .nav a.active{color:var(--accent)}

  .brand{position:absolute;top:10px;left:46px;width:282px;height:104px;background:var(--white);border-radius:0 0 8px 8px;z-index:3;display:flex;align-items:center;gap:12px;padding-left:22px;box-shadow:0 2px 6px rgba(0,0,0,.06)}
  .brand-dot{width:38px;height:38px;border-radius:50%;background:var(--accent);flex:none}
  .brand-name{font-size:19px;font-weight:500;color:var(--accent);line-height:1.15}

  .hero{position:absolute;top:96px;left:0;width:1200px;height:436px;background:linear-gradient(100deg,var(--hero-dark) 0%,var(--hero-mid) 35%,var(--hero-light) 62%,#a7a49d 100%)}
  .hero-copy{position:absolute;top:138px;left:610px;width:580px;color:var(--white);font-family:"Nothing You Could Do",cursive;font-size:36px;line-height:1.55}
  .hero-copy .line2{display:block;padding-left:78px}
  .hero-actions{position:absolute;top:290px;left:780px;display:flex;gap:52px}
  .hero-actions a{background:var(--accent);color:var(--white);text-decoration:none;font-family:"Roboto Condensed",Arial,sans-serif;font-weight:700;font-size:10px;padding:10px 13px;letter-spacing:.2px}
  .hero-dots{position:absolute;bottom:20px;left:592px;display:flex;gap:7px}
  .hero-dots span{width:9px;height:9px;border-radius:50%;background:var(--white);display:block}
  .hero-dots span.current{background:transparent;border:1px solid var(--white)}

  .welcome{position:absolute;top:532px;left:0;width:1200px;height:144px;background:linear-gradient(90deg,var(--band-from),var(--band-to));color:var(--white);text-align:center;padding:10px 56px 0}
  .welcome h1{font-family:"Roboto Condensed",Arial,sans-serif;font-weight:700;font-size:21px;padding-bottom:12px;border-bottom:1px dashed rgba(255,255,255,.85);margin:0 -10px 16px}
  .welcome p{font-family:"Roboto Condensed",Arial,sans-serif;font-size:13.5px;line-height:1.45;margin-bottom:22px}
</style>
</head>
<body>
  <div class="topbar">
    <span class="item"><svg viewBox="0 0 24 24"><path d="M6.6 10.8a15 15 0 0 0 6.6 6.6l2.2-2.2c.3-.3.7-.4 1-.2 1.1.4 2.3.6 3.6.6.6 0 1 .4 1 1V20c0 .6-.4 1-1 1A17 17 0 0 1 3 4c0-.6.4-1 1-1h3.5c.6 0 1 .4 1 1 0 1.3.2 2.5.6 3.6.1.3 0 .7-.2 1z"/></svg>+1 800 555 0142</span>
    <span class="item"><svg viewBox="0 0 24 24"><path d="M2 5h20v14H2z" fill="none" stroke="#7a7f86" stroke-width="2"/><path d="M2 5l10 8 10-8" fill="none" stroke="#7a7f86" stroke-width="2"/></svg>info@pinecrestholdingsgroup.example</span>
    <span class="sell-btn">Sell Your Home</span>
    <span class="social"><span></span><span></span></span>
  </div>

  <div class="brand">
    <span class="brand-dot"></span>
    <span class="brand-name">Pinecrest Holdings Group</span>
  </div>

  <nav class="nav">
    <a class="active" href="#">HOME</a>
    <a href="#">ABOUT US</a>
    <a href="#">PORTFOLIO</a>
    <a href="#">BLOG</a>
    <a href="#">CONTACT US</a>
  </nav>

  <section class="hero">
    <div class="hero-photo" role="img" aria-label="Photo of a renovated two-storey house with beige siding, a stone retaining wall and iron fence under bare misty trees" style="position:absolute;inset:0"></div>
    <p class="hero-copy">Investing in our neighborhood<span class="line2">Pinecrest Holdings Group</span></p>
    <div class="hero-actions">
      <a href="#">CALL NOW</a>
      <a href="#">GO ON SURFING</a>
    </div>
    <div class="hero-dots"><span class="current"></span><span></span><span></span><span></span></div>
  </section>

  <section class="welcome">
    <h1>Welcome We're Pinecrest Holdings Group</h1>
    <p>Pinecrest Holdings Group is a family run business with 3rd generation builders and renovators in the Morris County area. As the President and owner of Pinecrest Holdings Group I am dedicated to working hard to create opportunities for investment through real estate.</p>
    <p>At Pinecrest Holdings Group we have a valuable support system and a team of investors, realtors, attorneys, contractors and property managers providing a combined package offering years of</p>
  </section>
</body>
</html>
```